WordPress Design for both website and landing page for an expert

I need a clean and stylish design for my new website. I work as an expert (see attached file WHY HOW WHAT), my product is expert opinion (reports) for company evaluations You can use all of the attached pictures colored or black / white. The person is me, you can add other pictures, if you want. The design should be clean and stylish, so you could use white, black, gray, silver and / or one additional color. I have added an idea about my website, see attached file CONCEPT WEBSITE If you have any more information, please do not hesitate to contact us 'Hesitate to ask me ...

```html
<!DOCTYPE html>
<html lang="de">
<head>
<meta charset="utf-8">
<title>Jonas Kellner – Sachverständiger für Firmenbewertungen</title>
<link rel="stylesheet" href="https://fonts.googleapis.com/css2?family=Poppins:wght@300;400;500;600;700&display=swap">
<style>
  :root{
    --black:#0b0b0b;
    --white:#ffffff;
    --paper:#f5f5f5;
    --ink:#333333;
    --ink-soft:#555555;
    --grey:#6f6f6f;
    --line:#cfcfcf;
    --btn:#5a5a5a;
  }
  *{box-sizing:border-box;margin:0;padding:0}
  html,body{width:1200px;height:2757px;overflow:hidden}
  body{position:relative;background:var(--white);font-family:'Poppins',sans-serif;color:var(--ink)}
  .abs{position:absolute}

  /* Header */
  .topbar{left:0;top:0;width:1200px;height:56px;background:var(--black);z-index:5}
  .nav{top:0;height:56px;display:flex;align-items:center;gap:44px;color:var(--white);font-size:16px;font-weight:500;z-index:6}
  .nav.left{left:110px}
  .nav.right{left:802px}
  .brand-tab{left:432px;top:0;width:336px;height:122px;z-index:6}
  .brand-tab .brand-name{position:absolute;left:0;top:38px;width:336px;text-align:center;font-size:22px;font-weight:400;letter-spacing:3px;color:var(--grey)}

  /* Hero */
  .hero{left:0;top:0;width:1200px;height:640px;background:linear-gradient(90deg,#6d6557 0%,#b9b2a6 22%,#d9d5cf 50%,#b9b2a6 78%,#6d6557 100%);clip-path:polygon(0 0,100% 0,100% 551px,600px 634px,0 551px)}
  .hero-brand{left:0;top:222px;width:1200px;text-align:center;font-size:26px;font-weight:500;letter-spacing:4px;color:#e8e8e8}
  .hero-title{left:0;top:330px;width:1200px;text-align:center;font-size:39px;font-weight:500;color:var(--white)}
  .hero-sub{left:0;top:398px;width:1200px;text-align:center;font-size:23px;line-height:35px;font-weight:400;color:#f2f2f2}
  .dots{left:550px;top:561px;display:flex;gap:5px}
  .dots span{width:15px;height:15px;border-radius:50%;background:#cfcfcf}
  .dots span.on{background:var(--white)}

  /* Why choose us */
  .portrait-walk{left:0;top:551px;width:600px;height:745px;background:linear-gradient(180deg,#d8d6d0 0%,#bdbab3 50%,#8e8b84 100%);clip-path:polygon(0 0,600px 83px,600px 662px,0 745px)}
  .why{left:638px;top:684px;width:452px}
  .why h2{font-size:31px;font-weight:700;color:var(--ink);letter-spacing:.5px}
  .why .lead{margin-top:10px;font-size:19px;color:var(--ink)}
  .reason{margin-top:26px}
  .reason-head{display:flex;align-items:center;gap:14px}
  .num{width:38px;height:38px;border-radius:50%;background:#3a3a3a;color:var(--white);font-size:17px;font-weight:600;display:flex;align-items:center;justify-content:center}
  .reason-head h3{font-size:18px;font-weight:600;color:var(--black)}
  .reason p{margin-top:18px;font-size:13.5px;line-height:23px;color:var(--ink-soft);text-align:justify}

  .portrait-desk{left:600px;top:1213px;width:600px;height:625px;background:linear-gradient(160deg,#8b8884 0%,#5e5b57 45%,#2a2928 100%);clip-path:polygon(0 0,100% 0,100% 542px,0 625px)}
  .desk-copy{left:638px;top:1550px;width:452px;color:var(--white);font-size:15px;line-height:27px;text-align:justify;font-weight:400;z-index:2}
  .desk-copy p+p{margin-top:12px}

  /* FAQ */
  .faq{left:112px;top:1336px;width:469px;z-index:3}
  .faq h2{font-size:30px;font-weight:700;color:var(--ink)}
  .faq-list{margin-top:20px;display:flex;flex-direction:column;gap:16px}
  .faq-item{display:flex;justify-content:space-between;align-items:stretch;gap:10px;border:2px solid var(--line);background:var(--white);box-shadow:0 2px 5px rgba(0,0,0,.12);padding:5px 5px 5px 12px}
  .faq-item span{font-size:15px;line-height:21px;color:var(--black);padding:4px 0;flex:1}
  .faq-btn{flex:none;width:40px;min-height:30px;background:var(--btn);display:flex;align-items:center;justify-content:center}
  .faq-item.tall .faq-btn{align-items:flex-start;padding-top:12px}

  /* Quality promise */
  .promise-band{left:0;top:1755px;width:1200px;height:535px;background:var(--paper);clip-path:polygon(0 15px,600px 83px,1200px 0,100% 100%,0 100%);z-index:1}
  .promise{left:100px;top:1915px;width:1000px;text-align:center;z-index:2}
  .promise h2{font-size:30px;font-weight:700;color:var(--ink);letter-spacing:.5px}
  .promise .en{margin-top:18px;font-size:18px;line-height:31px;color:var(--black);padding:0 50px}
  .promise .de{margin-top:16px;font-size:15px;line-height:29px;color:var(--ink-soft);padding:0 30px}

  /* Footer */
  .footer{left:0;top:2178px;width:1200px;height:579px;background:var(--black);clip-path:polygon(0 82px,564px 0,100% 0,100% 100%,0 100%);z-index:2}
  .portrait-street{left:0;top:2178px;width:564px;height:579px;background:linear-gradient(90deg,#7c7c7c 0%,#9a9a9a 50%,#4a4a4a 100%);clip-path:polygon(0 82px,564px 0,564px 100%,0 100%);z-index:3}
  .foot-brand{left:564px;top:2380px;width:500px;text-align:center;font-size:30px;font-weight:300;letter-spacing:6px;color:var(--white);z-index:3}
  .pin{left:794px;top:2462px;z-index:3}
  .address{left:564px;top:2526px;width:500px;text-align:center;font-size:15px;line-height:27px;color:var(--white);z-index:3}
  .rule{left:602px;top:2634px;width:424px;height:1px;background:#555;z-index:3}
  .copyright{left:628px;top:2668px;font-size:13px;color:var(--white);z-index:3}
</style>
</head>
<body>

  <div class="abs hero" role="img" aria-label="Photo of stacked files and document folders in a warm office light"></div>
  <div class="abs hero-brand">JONAS KELLNER</div>
  <h1 class="abs hero-title">Sachverständiger für Firmenbewertungen</h1>
  <p class="abs hero-sub">Sie benötigen ein Gutachten zur Ermittlung des Wertes<br>Ihres Unternehmens</p>
  <div class="abs dots"><span class="on"></span><span></span><span></span><span></span><span></span></div>

  <header>
    <div class="abs topbar"></div>
    <nav class="abs nav left"><span>Home</span><span>What I Do</span><span>About Me</span></nav>
    <svg class="abs brand-tab" width="336" height="122" viewBox="0 0 336 122" aria-hidden="true">
      <polygon points="0,0 336,0 336,98 168,122 0,98" fill="#0b0b0b"/>
      <polygon points="4,0 332,0 332,94 168,114 4,94" fill="#ffffff"/>
    </svg>
    <div class="abs brand-tab" style="pointer-events:none;background:none"><div class="brand-name">JONAS KELLNER</div></div>
    <nav class="abs nav right"><span>Why I Do I &amp; How I Do It</span><span>Contact</span></nav>
  </header>

  <section>
    <div class="abs portrait-walk" role="img" aria-label="Photo of the expert in a dark suit walking along a bright office corridor"></div>
    <div class="abs why">
      <h2>WHY CHOOSE US</h2>
      <p class="lead">3 reasons, why you should work with me</p>
      <div class="reason">
        <div class="reason-head"><div class="num">1</div><h3>Schnell:</h3></div>
        <p>Sie bekommen Ihr Gutachten zeitnah (innerhalb von max. 21 Tagen nach Zugang aller benötigten Unterlagen).</p>
      </div>
      <div class="reason">
        <div class="reason-head"><div class="num">2</div><h3>Zertifiziert:</h3></div>
        <p>Sie erhalten ein qualifiziertes und belastbares Gutachten von einem zertifizierten Sachverständigen (höchste Akzeptanz bei allen Parteien).</p>
      </div>
      <div class="reason">
        <div class="reason-head"><div class="num">3</div><h3>Verständlich:</h3></div>
        <p>Ihr Gutachten wird für Sie logisch und nachvollziehbar sein und kein "Fachchinesisch" enthalten.</p>
      </div>
    </div>
  </section>

  <section>
    <div class="abs portrait-desk" role="img" aria-label="Photo of the expert in a white shirt seated at a desk, looking to the side"></div>
    <div class="abs desk-copy">
      <p>Lassen Sie Ihr Unternehmen von einem qualifizerten Sachverständigen bewerten und gehen somit vielen (unnötigen) Streitereien aus dem Weg.</p>
      <p>Merke: Die Kosten für ein Gutachten sind immer überproportional günstiger als die Kosten für Rechtsstreitigkeiten. Und das losgelöst von der psychischen Belastung einer solchen Auseinandersetzung ...</p>
    </div>

    <div class="abs faq">
      <h2>FAQ</h2>
      <div class="faq-list">
        <div class="faq-item"><span>What are the buying motives of the customers?</span><div class="faq-btn"><svg width="22" height="16" viewBox="0 0 22 16"><path d="M3 2l6 6-6 6M11 2l6 6-6 6" fill="none" stroke="#fff" stroke-width="2"/></svg></div></div>
        <div class="faq-item"><span>Was sind die Kaufmotive der Kunden?</span><div class="faq-btn"><svg width="22" height="16" viewBox="0 0 22 16"><path d="M3 2l6 6-6 6M11 2l6 6-6 6" fill="none" stroke="#fff" stroke-width="2"/></svg></div></div>
        <div class="faq-item tall"><span>Sie wollen Anteile Ihres Unternehmens oder ihr gesamtes Unternehmen verkaufen?</span><div class="faq-btn"><svg width="22" height="16" viewBox="0 0 22 16"><path d="M3 2l6 6-6 6M11 2l6 6-6 6" fill="none" stroke="#fff" stroke-width="2"/></svg></div></div>
        <div class="faq-item tall"><span>Sie wollen Ihr Unternehmen auf Ihre Erben übertragen und benötigen eine Bewertung für das Finanzamt?</span><div class="faq-btn"><svg width="22" height="16" viewBox="0 0 22 16"><path d="M3 2l6 6-6 6M11 2l6 6-6 6" fill="none" stroke="#fff" stroke-width="2"/></svg></div></div>
        <div class="faq-item tall"><span>Sie müssen im Rahmen einer Trennung/Scheidung jemanden ausbezahlen und benötigen eine Bemessungsgrundlage?</span><div class="faq-btn"><svg width="22" height="16" viewBox="0 0 22 16"><path d="M3 2l6 6-6 6M11 2l6 6-6 6" fill="none" stroke="#fff" stroke-width="2"/></svg></div></div>
      </div>
    </div>
  </section>

  <section>
    <div class="abs promise-band"></div>
    <div class="abs promise">
      <h2>MY QUALITY PROMISE</h2>
      <p class="en">should the advised date for the preparation of the report be exceeded, you will receive the report free of chare (I waive my fee)</p>
      <p class="de">Mein Qualitätsversprechen: Sollte der avisierte Termin für die Erstellung des Gutachtens überschritten werden, erhalten Sie das Gutachten absolut kostenfrei! (Ich verzichte</p>
    </div>
  </section>

  <footer>
    <div class="abs footer"></div>
    <div class="abs portrait-street" role="img" aria-label="Black and white photo of the expert in a three-piece suit standing on a city street"></div>
    <div class="abs foot-brand">JONAS KELLNER</div>
    <svg class="abs pin" width="40" height="44" viewBox="0 0 40 44" aria-hidden="true">
      <path d="M20 3c-8 0-14 6-14 14 0 10 14 24 14 24s14-14 14-24c0-8-6-14-14-14z" fill="none" stroke="#fff" stroke-width="3"/>
      <circle cx="20" cy="17" r="5" fill="none" stroke="#fff" stroke-width="3"/>
    </svg>
    <address class="abs address" style="font-style:normal">Jonas Kellner GmbH<br>Am Lindenhof 14<br>40210 Düsseldorf</address>
    <div class="abs rule"></div>
    <p class="abs copyright">Copyrights @ 2018 Jonas Kellner. All Rights Reserved.</p>
  </footer>

</body>
</html>
```